Plumberry Brochure - Tri Fold

Need to design a brochure for my business. Our colors are Pink/Black/White. I have included a new ad that I like the colors. This is a Cake Business that features gourmet cupcakes(retail and special order) , Custom Cakes for special occasions, Our retail shop which features our cupcakes, gelato, coffee, tea.

Focus should be on: Custom Cupcake orders for meetings, groups, schools, etc (catering).. Custom Cakes (special events - weddings, birthdays etc., Retail Sales (cupcakes, gelato, coffee, tea espresso at our Shop, Decorating Classes/birthday parties.

See our sample brochure and advertisements for colors and some content

Like to have a map on the back with our address, website, phone number

We will guaranty payment

Target Market(s)

People ordering cupcakes for meetings, parties, events, school functions
Retail customers coming to our shop to enjoy our products
People ordering custom cakes for their special occasions
Cake Decorating classes/Birthday parties

Industry/Entity Type

Retail

Font styles to use
Serif
Sans Serif

Colors
ffffff
e567a6
1b1b1b
ebebeb

Requirements
Must have
• Custom Cupcake orders
Custom Cakes
Retail Customers

website
telephone numbers
facebook page
address
hours of operation
Nice to have
• The custom orders are the priority
followed by the retail
followed by cake decorating classes/birthday parties

```html
<!DOCTYPE html>
<html lang="en">
<head>
<meta charset="utf-8">
<title>The Plumberry Cake House – Tri-fold Brochure</title>
<link href="https://fonts.googleapis.com/css2?family=Libre+Baskerville:wght@400;700&family=Arimo:wght@400;700&display=swap" rel="stylesheet">
<style>
  :root{
    --pink:#e567a6;
    --ink:#1b1b1b;
    --white:#ffffff;
    --light:#ebebeb;
    --paper:#eee4d7;
    --grey-text:#4a4a4a;
    --stage:#d8d2cb;
  }
  *{margin:0;padding:0;box-sizing:border-box}
  html,body{width:1200px;height:943px;overflow:hidden;background:var(--stage)}
  .brochure{position:absolute;left:35px;top:35px;width:1130px;height:872px;background:var(--paper);box-shadow:0 2px 10px rgba(0,0,0,.35)}
  .panel{position:absolute;top:0;height:872px;width:377px;overflow:hidden}
  .panel--classes{left:0}
  .panel--contact{left:377px;width:376px}
  .panel--hours{left:753px}
  .photo{position:absolute;left:0;top:0;width:100%}
  .photo--cupcakes{height:320px;background:linear-gradient(160deg,#f3d9dc 0%,#c9d9a8 45%,#f2b8cc 100%)}
  .photo--gelato{height:270px;background:radial-gradient(ellipse at 50% 45%,#f6c248 0%,#f9dc8a 45%,#ffffff 75%)}
  .photo--cake{height:440px;background:linear-gradient(180deg,#e8ecd0 0%,#7cb8c9 45%,#6aa8bb 75%,#4d6e3a 100%)}
  .flourish{position:absolute;left:0;width:100%;height:64px;background:linear-gradient(180deg,rgba(229,103,166,0) 0%,rgba(229,103,166,.55) 50%,rgba(229,103,166,0) 100%)}
  .panel--classes .flourish{top:258px}
  .panel--contact .flourish{top:250px}
  .panel--hours .flourish{top:400px}
  .classes-title{position:absolute;left:0;top:398px;width:377px;text-align:center;font:700 24px/36px "Libre Baskerville",Georgia,serif;color:var(--ink)}
  .classes-copy{position:absolute;left:33px;top:475px;width:315px;font:400 13.5px/17px "Arimo",Arial,sans-serif;letter-spacing:-0.25px;color:var(--grey-text);text-align:justify}
  .classes-copy p{margin-bottom:10px}
  .classes-copy .cta{font-weight:700;color:var(--ink);text-align:center;margin-top:16px;letter-spacing:0}
  .services{position:absolute;left:0;top:322px;width:376px;list-style:none;text-align:center;font:700 12px/20px "Arimo",Arial,sans-serif;color:var(--ink)}
  .services .accent{color:var(--pink)}
  .map{position:absolute;left:88px;top:395px;width:268px;height:150px;border:2px solid var(--ink);border-radius:12px;background:linear-gradient(135deg,#e4e8e2,#d6dfd0 50%,#e9e4d8);box-shadow:0 2px 4px rgba(0,0,0,.35)}
  .nameplate{position:absolute;display:flex;align-items:center;justify-content:center;gap:10px;color:var(--pink);font:700 20px/1.2 "Libre Baskerville",Georgia,serif;text-align:center}
  .nameplate .dot{width:12px;height:12px;border-radius:50%;background:var(--pink);flex:none}
  .panel--contact .nameplate{left:0;top:640px;width:376px}
  .panel--hours .nameplate{left:0;top:540px;width:377px;font-size:21px}
  .contact-call{position:absolute;left:0;top:722px;width:376px;text-align:center;font:700 20px/1 "Arimo",Arial,sans-serif;color:var(--grey-text)}
  .contact-wifi{position:absolute;left:0;top:755px;width:376px;text-align:center;font:700 18px/1 "Arimo",Arial,sans-serif;color:var(--grey-text)}
  .contact-logon{position:absolute;left:0;top:780px;width:376px;text-align:center;font:700 11.5px/1 "Arimo",Arial,sans-serif;color:var(--ink)}
  .contact-social{position:absolute;left:0;top:796px;width:376px;text-align:center;font:700 11.5px/1 "Arimo",Arial,sans-serif;color:var(--ink)}
  .tagline{position:absolute;left:0;top:596px;width:377px;text-align:center;font:700 22px/1 "Libre Baskerville",Georgia,serif;color:var(--ink)}
  .hours{position:absolute;left:0;top:630px;width:377px;text-align:center;list-style:none;font:700 15.5px/28px "Libre Baskerville",Georgia,serif;color:var(--ink)}
  .footer{position:absolute;left:0;top:810px;width:100%;height:62px;text-align:center;border-top:2px solid var(--ink)}
  .panel--classes .footer{background:linear-gradient(90deg,var(--ink) 0%,#3a3a3a 60%,#7a7a7a 100%);color:var(--white)}
  .panel--contact .footer{background:linear-gradient(90deg,var(--ink) 0%,#5a3a4a 55%,var(--pink) 100%);color:var(--white);border-top:2px solid var(--pink)}
  .panel--hours .footer{background:var(--paper);color:var(--ink)}
  .footer-call{font:700 20px/1 "Libre Baskerville",Georgia,serif;padding-top:11px}
  .footer-web{font:700 13px/1 "Libre Baskerville",Georgia,serif;padding-top:8px}
  .footer-address{font:400 13px/17px "Arimo",Arial,sans-serif;padding:8px 24px 0}
</style>
</head>
<body>
<main class="brochure">

  <section class="panel panel--classes">
    <div class="photo photo--cupcakes" role="img" aria-label="Photo of frosted cupcakes with pink, green and white swirls and sugar butterflies"></div>
    <div class="flourish" role="img" aria-label="Pink scroll ornament"></div>
    <h2 class="classes-title">Cake Decorating Classes<br>and Parties</h2>
    <div class="classes-copy">
      <p>TPCH offers a variety of cake decorating classes. Whether you are an amateur who has never baked a cake, or a more advanced cake decorator, there is something for you in our selection of classes.</p>
      <p>In our classes you will learn the best expert decorating techniques for cakes, cookies, cupcakes and cake-pops.</p>
      <p>All our classes are “hands-on,” so when the class is over you will have a creation to take home to show and savor with your loved ones. We will use the same tools and methods as we do when making our own cakes in our shop.</p>
      <p>Many of our sessions will be taught by a master cake decorator and culinary arts instructor.</p>
      <p>Classes are conducted in small groups, allowing for personal attention to each student. You should reserve your place ahead of time to ensure a space</p>
      <p class="cta">Please call for more details and the schedule.</p>
    </div>
    <footer class="footer">
      <div class="footer-call">Call Us :&nbsp; 555-013-4827</div>
      <div class="footer-web">www.theplumberrycakehouse.com</div>
    </footer>
  </section>

  <section class="panel panel--contact">
    <div class="photo photo--gelato" role="img" aria-label="Photo of scoops of mango gelato in a glass bowl"></div>
    <div class="flourish" role="img" aria-label="Pink scroll ornament"></div>
    <ul class="services">
      <li><span class="accent">Custom Cupcake Orders</span> for Meetings, Schools &amp; Events</li>
      <li><span class="accent">Custom Cakes</span> for Weddings, Birthdays &amp; More</li>
      <li><span class="accent">Our Shop:</span> Cupcakes · Gelato · Coffee · Tea · Espresso</li>
    </ul>
    <div class="map" role="img" aria-label="Street map marking the shop location"></div>
    <div class="nameplate"><span class="dot"></span>The Plumberry Cake House</div>
    <p class="contact-call">Call Us :&nbsp; (555) 013-4827</p>
    <p class="contact-wifi">Free WiFi</p>
    <p class="contact-logon">Log On : www.ThePlumberryCakeHouse.com</p>
    <p class="contact-social">Facebook : facebook.com/ThePlumberryCakeHouse</p>
    <footer class="footer">
      <div class="footer-address">Located in Lake Maple Center 4120 Maple Grove Blvd&nbsp; Lake Haven, Florida&nbsp; 33400</div>
    </footer>
  </section>

  <section class="panel panel--hours">
    <div class="photo photo--cake" role="img" aria-label="Photo of a three-tier blue celebration cake decorated with trees, clouds, a sun and toy trains"></div>
    <div class="flourish" role="img" aria-label="Pink scroll ornament"></div>
    <div class="nameplate"><span class="dot"></span>The Plumberry Cake House</div>
    <h2 class="tagline">It’s Love at First Bite</h2>
    <ul class="hours">
      <li>Hours:</li>
      <li>Monday:&nbsp; By Appointment</li>
      <li>Tuesday-Thursday 11-7</li>
      <li>Friday 11-10</li>
      <li>Saturday 10-10</li>
      <li>Sunday 11-7</li>
    </ul>
    <footer class="footer">
      <div class="footer-call">Call Us :&nbsp; 555-013-4827</div>
      <div class="footer-web">www.theplumberrycakehouse.com</div>
    </footer>
  </section>

</main>
</body>
</html>
```